A clean crisp business card for a Landscape Construction company. Designed to be easy to read contact/ info and also be appealing/interesting, unlike a traditional business card.

Industry/Entity Type

Landscape Construction

Contact Information for Business Card

Company name : Brambleford Landscape Construction, phone number: (877) 62Vista, website:Bramblefordyards.example, Email, sales@bramblefordyards.example

Requirements
Nice to have
• Luxurious finishes/ details…. Icons or emblems next to contact info
Should not have
• Clipart or general pictures

```html
<!DOCTYPE html>
<html lang="en">
<head>
<meta charset="utf-8">
<title>Brambleford Landscape Construction – Business Card</title>
<link href="https://fonts.googleapis.com/css2?family=Cinzel:wght@400;600&family=Arimo:wght@400&display=swap" rel="stylesheet">
<style>
  :root {
    --stage: #1f1f1f;
    --brand-blue: #1565c0;
    --brand-green: #9ccb3b;
    --front-mid: #4a9a86;
    --ink: #161616;
    --paper: #ffffff;
    --rule: #b9b9b9;
  }
  * { box-sizing: border-box; margin: 0; padding: 0; }
  html, body {
    width: 1200px; height: 1015px; overflow: hidden;
    background: var(--stage);
  }
  .stage {
    width: 1200px; height: 1015px;
    display: flex; flex-direction: column; align-items: center; justify-content: center;
    gap: 56px;
  }
  .card {
    width: 760px; height: 434px; position: relative; overflow: hidden;
    box-shadow: 0 18px 40px rgba(0,0,0,.55);
  }

  /* Front */
  .card-front {
    background: linear-gradient(200deg, var(--brand-green) 0%, #7fb457 30%, var(--front-mid) 62%, var(--brand-blue) 100%);
    display: flex; align-items: center; justify-content: center;
  }
  .card-front .emblem-area {
    position: absolute; left: 40px; top: 30px; width: 380px; height: 380px; border-radius: 50%;
    background: radial-gradient(circle, rgba(21,101,192,.35) 0%, rgba(21,101,192,.12) 55%, rgba(255,255,255,0) 72%);
  }
  .wordmark {
    position: relative; display: flex; align-items: center; gap: 16px;
    font-family: "Cinzel", serif; font-weight: 600; letter-spacing: .06em; text-transform: uppercase;
  }
  .wordmark-dot { width: 18px; height: 18px; border-radius: 50%; flex: none; }
  .wordmark-text { line-height: 1.15; }
  .card-front .wordmark { color: var(--paper); font-size: 30px; }
  .card-front .wordmark-dot { background: var(--paper); }

  /* Back */
  .card-back { background: var(--paper); }
  .card-back .wordmark {
    position: absolute; left: 56px; top: 150px; width: 330px;
    color: var(--brand-blue); font-size: 24px;
  }
  .card-back .wordmark-dot { background: var(--brand-blue); }
  .divider { position: absolute; inset: 0; }
  .contact {
    position: absolute; left: 430px; top: 58px; width: 310px;
    font-family: "Arimo", sans-serif; color: var(--ink);
  }
  .person-name {
    font-family: "Cinzel", serif; font-weight: 400; font-size: 27px; color: var(--brand-blue);
    letter-spacing: .02em; line-height: 1;
  }
  .person-name .surname { color: var(--brand-green); }
  .person-role {
    margin-top: 4px; font-size: 15px; letter-spacing: .03em; color: var(--brand-green); text-transform: uppercase;
  }
  .contact-list { list-style: none; margin-top: 18px; }
  .contact-list li { display: flex; align-items: center; gap: 8px; font-size: 15px; line-height: 1.5; }
  .contact-list svg { width: 15px; height: 15px; flex: none; fill: var(--brand-blue); }
  .contact-list .accent { color: var(--brand-blue); }
  .address { margin-top: 14px; font-size: 15px; line-height: 1.4; padding-left: 23px; }
  .band-blue { position: absolute; left: 0; bottom: 0; width: 450px; height: 14px; background: var(--brand-blue); }
  .band-green { position: absolute; right: 0; bottom: 0; width: 304px; height: 110px; background: var(--brand-green); }
</style>
</head>
<body>
<main class="stage">
  <section class="card card-front" aria-label="Card front">
    <div class="emblem-area" role="img" aria-label="Soft decorative glow in brand blue"></div>
    <div class="wordmark">
      <span class="wordmark-dot"></span>
      <span class="wordmark-text">Brambleford<br>Landscape Construction</span>
    </div>
  </section>

  <section class="card card-back" aria-label="Card back">
    <div class="wordmark">
      <span class="wordmark-dot"></span>
      <span class="wordmark-text">Brambleford<br>Landscape Construction</span>
    </div>

    <svg class="divider" viewBox="0 0 760 434" aria-hidden="true">
      <line x1="400" y1="40" x2="430" y2="300" stroke="var(--rule)" stroke-width="1"/>
    </svg>

    <div class="contact">
      <h1 class="person-name">Owen <span class="surname">Hartley</span></h1>
      <p class="person-role">Managing Director</p>
      <ul class="contact-list">
        <li>
          <svg viewBox="0 0 24 24"><path d="M6.6 10.8a15.1 15.1 0 0 0 6.6 6.6l2.2-2.2a1 1 0 0 1 1-.25 11.4 11.4 0 0 0 3.6.57 1 1 0 0 1 1 1V20a1 1 0 0 1-1 1A17 17 0 0 1 3 4a1 1 0 0 1 1-1h3.5a1 1 0 0 1 1 1c0 1.25.2 2.45.57 3.6a1 1 0 0 1-.25 1z"/></svg>
          (555) 010-4477
        </li>
        <li>
          <svg viewBox="0 0 24 24"><path d="M2 5h20v14H2z M2 5l10 8 10-8" fill="none" stroke="var(--brand-blue)" stroke-width="2.2"/></svg>
          sales@bramblefordyards.example
        </li>
        <li>
          <svg viewBox="0 0 24 24"><circle cx="12" cy="12" r="9.5" fill="none" stroke="var(--brand-blue)" stroke-width="2"/><path d="M2.5 12h19M12 2.5c3 3 3 16 0 19M12 2.5c-3 3-3 16 0 19" fill="none" stroke="var(--brand-blue)" stroke-width="1.6"/></svg>
          <span><span class="accent">Bramblefordyards</span>.example</span>
        </li>
      </ul>
      <p class="address">421, Address line goes here<br>45452, Country Name</p>
    </div>

    <div class="band-blue"></div>
    <div class="band-green"></div>
  </section>
</main>
</body>
</html>
```